Dental Medical History Form - Content provided

Design a medical history form for a dental practice. Content is provided so all that is needed is the formatting to make it look great and easy to read.

"Patient Information" to include all information contained in top portion of the "Patient Medical History Form" docx file.

"Medical History" should follow the formatting and content of the "Exact Medical History" file as this is what the entry fields look like in our practice software and so we would like it to match.

1st page - Patient info, allergies, medications, antibiotics, joint replacement, pregnancy.

2nd page - Do you have, or have you had, any of the following? . . . . . . .
Updates

Target Market(s)

All ages but must be clear enough for elderly to read. Use as much space as possible to keep font size bigger yet keep to two pages

Industry/Entity Type

Dental

Font styles to use
Sans Serif

Requirements
Must have
• All content provided
• Our logo at the top (file provided)
• Century Gothic Font
• Limit to two pages

```html
<!DOCTYPE html>
<html lang="en">
<head>
<meta charset="utf-8">
<title>Medical History Form – Page 2</title>
<link rel="stylesheet" href="https://fonts.googleapis.com/css2?family=PT+Sans:ital,wght@0,400;0,700;1,400;1,700&display=swap">
<style>
  :root {
    --backdrop: #e8e7e5;
    --paper: #fbfbfa;
    --edge-band: #d9d4cf;
    --ink: #3a3a3a;
    --ink-soft: #5b5b5b;
    --box-fill: #ebe8e5;
    --box-line: #c9c4bf;
    --rule: #9a9a9a;
  }
  * { box-sizing: border-box; margin: 0; padding: 0; }
  html, body {
    width: 1200px; height: 784px; overflow: hidden;
    background: var(--backdrop);
    font-family: "PT Sans", sans-serif;
    color: var(--ink);
  }
  .form-page {
    position: absolute; left: 20px; top: 18px;
    width: 1160px; height: 748px;
    background: var(--paper);
    border-top: 8px solid var(--edge-band);
    border-bottom: 8px solid var(--edge-band);
    box-shadow: 0 2px 6px rgba(0,0,0,.12);
  }
  .form-title {
    position: absolute; right: 40px; top: 14px;
    font-size: 16px; font-weight: 700; font-style: italic;
  }
  .history-column {
    position: absolute; top: 40px;
    list-style: none;
  }
  .history-column.left { left: 60px; }
  .history-column.right { left: 600px; top: 58px; }
  .history-row {
    display: grid;
    grid-template-columns: 260px 20px 16px 18px 16px;
    align-items: center; column-gap: 4px;
    height: 15px;
    font-size: 11.5px; font-style: italic; color: var(--ink-soft);
  }
  .history-row.section-head {
    font-weight: 700; color: var(--ink); font-style: normal;
  }
  .answer-label { font-size: 10px; font-style: italic; }
  .tick-box {
    width: 12px; height: 11px;
    background: var(--box-fill);
    border: 1px solid var(--box-line);
  }
  .sign-off {
    position: absolute; left: 60px; right: 60px; bottom: 56px;
    display: flex; gap: 80px;
    font-weight: 700; font-style: italic; font-size: 13px;
  }
  .sign-field { display: flex; align-items: flex-end; gap: 10px; }
  .sign-field.date { width: 330px; }
  .sign-field.signature { flex: 1; }
  .sign-line { flex: 1; border-bottom: 1px solid var(--rule); height: 14px; }
  .closing-note {
    position: absolute; left: 60px; bottom: 18px;
    font-size: 10px; font-style: italic; color: var(--ink-soft); line-height: 1.35;
  }
</style>
</head>
<body>
<main class="form-page">
  <h1 class="form-title">Do you have, or have you had, any of the following?</h1>

  <ul class="history-column left">
    <li class="history-row section-head"><span>Dental</span></li>
    <li class="history-row"><span>Acid Reflux</span><span class="answer-label">Yes</span><span class="tick-box"></span><span class="answer-label">No</span><span class="tick-box"></span></li>
    <li class="history-row"><span>Bad Breath/Taste</span><span class="answer-label">Yes</span><span class="tick-box"></span><span class="answer-label">No</span><span class="tick-box"></span></li>
    <li class="history-row"><span>Bleeding/Swollen/Sore Gums</span><span class="answer-label">Yes</span><span class="tick-box"></span><span class="answer-label">No</span><span class="tick-box"></span></li>
    <li class="history-row"><span>Blisters/Ulcers in Mouth</span><span class="answer-label">Yes</span><span class="tick-box"></span><span class="answer-label">No</span><span class="tick-box"></span></li>
    <li class="history-row"><span>Broken tooth/filling</span><span class="answer-label">Yes</span><span class="tick-box"></span><span class="answer-label">No</span><span class="tick-box"></span></li>
    <li class="history-row"><span>Burning tongue</span><span class="answer-label">Yes</span><span class="tick-box"></span><span class="answer-label">No</span><span class="tick-box"></span></li>
    <li class="history-row"><span>Dry mouth</span><span class="answer-label">Yes</span><span class="tick-box"></span><span class="answer-label">No</span><span class="tick-box"></span></li>
    <li class="history-row"><span>Food collection between teeth</span><span class="answer-label">Yes</span><span class="tick-box"></span><span class="answer-label">No</span><span class="tick-box"></span></li>
    <li class="history-row"><span>Grinding/clenching teeth (day/night)</span><span class="answer-label">Yes</span><span class="tick-box"></span><span class="answer-label">No</span><span class="tick-box"></span></li>
    <li class="history-row"><span>Loose teeth</span><span class="answer-label">Yes</span><span class="tick-box"></span><span class="answer-label">No</span><span class="tick-box"></span></li>
    <li class="history-row"><span>Crooked teeth</span><span class="answer-label">Yes</span><span class="tick-box"></span><span class="answer-label">No</span><span class="tick-box"></span></li>
    <li class="history-row"><span>Discoloured teeth</span><span class="answer-label">Yes</span><span class="tick-box"></span><span class="answer-label">No</span><span class="tick-box"></span></li>
    <li class="history-row"><span>Sensitivity to Hot/Cold</span><span class="answer-label">Yes</span><span class="tick-box"></span><span class="answer-label">No</span><span class="tick-box"></span></li>
    <li class="history-row"><span>Tooth pain when chewing</span><span class="answer-label">Yes</span><span class="tick-box"></span><span class="answer-label">No</span><span class="tick-box"></span></li>
    <li class="history-row"><span>Jaw pain/Fracture</span><span class="answer-label">Yes</span><span class="tick-box"></span><span class="answer-label">No</span><span class="tick-box"></span></li>
    <li class="history-row"><span>Orthodontic treatment/history</span><span class="answer-label">Yes</span><span class="tick-box"></span><span class="answer-label">No</span><span class="tick-box"></span></li>
    <li class="history-row"><span>Oral Cancer</span><span class="answer-label">Yes</span><span class="tick-box"></span><span class="answer-label">No</span><span class="tick-box"></span></li>
    <li class="history-row section-head"><span>Diet/Lifestyle</span></li>
    <li class="history-row"><span>Drink more than one glass alcohol per day</span><span class="answer-label">Yes</span><span class="tick-box"></span><span class="answer-label">No</span><span class="tick-box"></span></li>
    <li class="history-row"><span>Smoking</span><span class="answer-label">Yes</span><span class="tick-box"></span><span class="answer-label">No</span><span class="tick-box"></span></li>
    <li class="history-row"><span>Carbonated drinks</span><span class="answer-label">Yes</span><span class="tick-box"></span><span class="answer-label">No</span><span class="tick-box"></span></li>
    <li class="history-row"><span>Sugary foods</span><span class="answer-label">Yes</span><span class="tick-box"></span><span class="answer-label">No</span><span class="tick-box"></span></li>
    <li class="history-row section-head"><span>Blood</span></li>
    <li class="history-row"><span>Anaemia</span><span class="answer-label">Yes</span><span class="tick-box"></span><span class="answer-label">No</span><span class="tick-box"></span></li>
    <li class="history-row"><span>Blood Clots</span><span class="answer-label">Yes</span><span class="tick-box"></span><span class="answer-label">No</span><span class="tick-box"></span></li>
    <li class="history-row"><span>Leukemia</span><span class="answer-label">Yes</span><span class="tick-box"></span><span class="answer-label">No</span><span class="tick-box"></span></li>
    <li class="history-row"><span>Low platelets</span><span class="answer-label">Yes</span><span class="tick-box"></span><span class="answer-label">No</span><span class="tick-box"></span></li>
    <li class="history-row"><span>Lymphoma</span><span class="answer-label">Yes</span><span class="tick-box"></span><span class="answer-label">No</span><span class="tick-box"></span></li>
    <li class="history-row"><span>Haemophilia</span><span class="answer-label">Yes</span><span class="tick-box"></span><span class="answer-label">No</span><span class="tick-box"></span></li>
    <li class="history-row section-head"><span>Chest</span></li>
    <li class="history-row"><span>Bronchitis</span><span class="answer-label">Yes</span><span class="tick-box"></span><span class="answer-label">No</span><span class="tick-box"></span></li>
    <li class="history-row"><span>Cystic Fibrosis</span><span class="answer-label">Yes</span><span class="tick-box"></span><span class="answer-label">No</span><span class="tick-box"></span></li>
    <li class="history-row"><span>Emphysema</span><span class="answer-label">Yes</span><span class="tick-box"></span><span class="answer-label">No</span><span class="tick-box"></span></li>
    <li class="history-row"><span>Pneumonia</span><span class="answer-label">Yes</span><span class="tick-box"></span><span class="answer-label">No</span><span class="tick-box"></span></li>
    <li class="history-row section-head"><span>Infectious Disease</span></li>
    <li class="history-row"><span>Creutzfeldt-Jakob Disease</span><span class="answer-label">Yes</span><span class="tick-box"></span><span class="answer-label">No</span><span class="tick-box"></span></li>
    <li class="history-row"><span>Hepatitis A,B,C,D</span><span class="answer-label">Yes</span><span class="tick-box"></span><span class="answer-label">No</span><span class="tick-box"></span></li>
  </ul>

  <ul class="history-column right">
    <li class="history-row"><span>HIV/AIDS</span><span class="answer-label">Yes</span><span class="tick-box"></span><span class="answer-label">No</span><span class="tick-box"></span></li>
    <li class="history-row"><span>Influenza</span><span class="answer-label">Yes</span><span class="tick-box"></span><span class="answer-label">No</span><span class="tick-box"></span></li>
    <li class="history-row"><span>Shingles</span><span class="answer-label">Yes</span><span class="tick-box"></span><span class="answer-label">No</span><span class="tick-box"></span></li>
    <li class="history-row"><span>Tuberculosis</span><span class="answer-label">Yes</span><span class="tick-box"></span><span class="answer-label">No</span><span class="tick-box"></span></li>
    <li class="history-row section-head"><span>Heart</span></li>
    <li class="history-row"><span>Angina</span><span class="answer-label">Yes</span><span class="tick-box"></span><span class="answer-label">No</span><span class="tick-box"></span></li>
    <li class="history-row"><span>Atrial Fibrillation</span><span class="answer-label">Yes</span><span class="tick-box"></span><span class="answer-label">No</span><span class="tick-box"></span></li>
    <li class="history-row"><span>Blood Pressure (High/Low)</span><span class="answer-label">Yes</span><span class="tick-box"></span><span class="answer-label">No</span><span class="tick-box"></span></li>
    <li class="history-row"><span>Congenital Heart Disease</span><span class="answer-label">Yes</span><span class="tick-box"></span><span class="answer-label">No</span><span class="tick-box"></span></li>
    <li class="history-row"><span>Heart attack</span><span class="answer-label">Yes</span><span class="tick-box"></span><span class="answer-label">No</span><span class="tick-box"></span></li>
    <li class="history-row"><span>Heart murmur</span><span class="answer-label">Yes</span><span class="tick-box"></span><span class="answer-label">No</span><span class="tick-box"></span></li>
    <li class="history-row"><span>Heart surgery</span><span class="answer-label">Yes</span><span class="tick-box"></span><span class="answer-label">No</span><span class="tick-box"></span></li>
    <li class="history-row"><span>Heart valve replacement</span><span class="answer-label">Yes</span><span class="tick-box"></span><span class="answer-label">No</span><span class="tick-box"></span></li>
    <li class="history-row"><span>Infective endocarditis</span><span class="answer-label">Yes</span><span class="tick-box"></span><span class="answer-label">No</span><span class="tick-box"></span></li>
    <li class="history-row"><span>Rheumatic Heart Disease</span><span class="answer-label">Yes</span><span class="tick-box"></span><span class="answer-label">No</span><span class="tick-box"></span></li>
    <li class="history-row"><span>Pacemaker</span><span class="answer-label">Yes</span><span class="tick-box"></span><span class="answer-label">No</span><span class="tick-box"></span></li>
    <li class="history-row"><span>Stent</span><span class="answer-label">Yes</span><span class="tick-box"></span><span class="answer-label">No</span><span class="tick-box"></span></li>
    <li class="history-row section-head"><span>Other</span></li>
    <li class="history-row"><span>Anxiety/PTSD</span><span class="answer-label">Yes</span><span class="tick-box"></span><span class="answer-label">No</span><span class="tick-box"></span></li>
    <li class="history-row"><span>Arthritis</span><span class="answer-label">Yes</span><span class="tick-box"></span><span class="answer-label">No</span><span class="tick-box"></span></li>
    <li class="history-row"><span>Alzheimer's</span><span class="answer-label">Yes</span><span class="tick-box"></span><span class="answer-label">No</span><span class="tick-box"></span></li>
    <li class="history-row"><span>Asthma</span><span class="answer-label">Yes</span><span class="tick-box"></span><span class="answer-label">No</span><span class="tick-box"></span></li>
    <li class="history-row"><span>Anaphylaxis</span><span class="answer-label">Yes</span><span class="tick-box"></span><span class="answer-label">No</span><span class="tick-box"></span></li>
    <li class="history-row"><span>Auto-immune disease</span><span class="answer-label">Yes</span><span class="tick-box"></span><span class="answer-label">No</span><span class="tick-box"></span></li>
    <li class="history-row"><span>Coeliac</span><span class="answer-label">Yes</span><span class="tick-box"></span><span class="answer-label">No</span><span class="tick-box"></span></li>
    <li class="history-row"><span>Depression</span><span class="answer-label">Yes</span><span class="tick-box"></span><span class="answer-label">No</span><span class="tick-box"></span></li>
    <li class="history-row"><span>Diabetes</span><span class="answer-label">Yes</span><span class="tick-box"></span><span class="answer-label">No</span><span class="tick-box"></span></li>
    <li class="history-row"><span>Epilepsy</span><span class="answer-label">Yes</span><span class="tick-box"></span><span class="answer-label">No</span><span class="tick-box"></span></li>
    <li class="history-row"><span>Kidney Disease</span><span class="answer-label">Yes</span><span class="tick-box"></span><span class="answer-label">No</span><span class="tick-box"></span></li>
    <li class="history-row"><span>Liver Disease</span><span class="answer-label">Yes</span><span class="tick-box"></span><span class="answer-label">No</span><span class="tick-box"></span></li>
    <li class="history-row"><span>Osteoporosis</span><span class="answer-label">Yes</span><span class="tick-box"></span><span class="answer-label">No</span><span class="tick-box"></span></li>
    <li class="history-row"><span>Parkinson's</span><span class="answer-label">Yes</span><span class="tick-box"></span><span class="answer-label">No</span><span class="tick-box"></span></li>
    <li class="history-row"><span>Radiation to Head/Neck</span><span class="answer-label">Yes</span><span class="tick-box"></span><span class="answer-label">No</span><span class="tick-box"></span></li>
    <li class="history-row"><span>Schizophrenia</span><span class="answer-label">Yes</span><span class="tick-box"></span><span class="answer-label">No</span><span class="tick-box"></span></li>
    <li class="history-row"><span>Snoring</span><span class="answer-label">Yes</span><span class="tick-box"></span><span class="answer-label">No</span><span class="tick-box"></span></li>
    <li class="history-row"><span>Sleep apnea</span><span class="answer-label">Yes</span><span class="tick-box"></span><span class="answer-label">No</span><span class="tick-box"></span></li>
    <li class="history-row"><span>Stroke</span><span class="answer-label">Yes</span><span class="tick-box"></span><span class="answer-label">No</span><span class="tick-box"></span></li>
  </ul>

  <div class="sign-off">
    <div class="sign-field date"><span>Date</span><span class="sign-line"></span></div>
    <div class="sign-field signature"><span>Signature</span><span class="sign-line"></span></div>
  </div>

  <p class="closing-note">Thank you for the time to complete your medical history form.<br>
  Oral health is linked to overall health and this comprehensive questionnaire will help us to provide you with optimal and safe care.</p>
</main>
</body>
</html>
```